Larkspur Cosmetics Website needs a professional upgrade

I need a new design for an online cosmetics store that looks professional and clean but also has a natural look and feel to it.

The women in the top bar (Image attached) needs to be included and she is on all of our advertising banners/ stands though I would like to come away from the black.

Design Needs:
- 1 x Home Page
- 1 x Products Page

I have plenty more website coming along so hopefully can find someone who I can rely on for a quick turnover :)

Happy designing !

Industry/Entity Type

Store

Number of Pages Required

2 page

Font styles to use
Sans Serif

Requirements
Must have
• - Natural Clean look
Should not have
• - The current black and green colours

```html
<!DOCTYPE html>
<html lang="en">
<head>
<meta charset="utf-8">
<title>Larkspur Cosmetics</title>
<link rel="stylesheet" href="https://fonts.googleapis.com/css2?family=Roboto+Condensed:wght@300;400;700&family=Roboto:wght@400;500&display=swap">
<style>
:root{
  --gold:#9b8650;
  --gold-dark:#85723f;
  --gold-line:#b6a473;
  --ink:#333333;
  --muted:#555555;
  --white:#ffffff;
  --light:#f3f3f3;
  --rule:#dddddd;
  --head:"Roboto Condensed", Arial, sans-serif;
  --body:"Roboto", Arial, sans-serif;
}
*{box-sizing:border-box;margin:0;padding:0}
html,body{width:1200px;height:3711px;overflow:hidden}
body{font-family:var(--body);color:var(--ink);background:var(--white);position:relative}
a{color:inherit;text-decoration:none}
.wrap{width:1046px;margin:0 auto;position:relative}

/* top bar */
.topbar{height:54px;background:var(--gold);color:var(--white);font-size:14px}
.topbar .wrap{display:flex;justify-content:space-between;align-items:center;height:54px}
.follow{display:flex;align-items:center;gap:10px}
.dot-icon{width:16px;height:16px;border-radius:50%;background:var(--white)}
.shop-links{display:flex;gap:36px;align-items:center}
.shop-links span{display:flex;align-items:center;gap:9px}

/* header */
.header{height:114px;border-bottom:1px solid var(--rule)}
.header .wrap{height:114px}
.call{position:absolute;left:0;top:26px;display:flex;gap:14px;align-items:center}
.call small{display:block;font-size:13px;color:var(--ink)}
.call strong{font-family:var(--head);font-size:29px;font-weight:700;color:var(--ink);line-height:1}
.brand{position:absolute;left:50%;top:4px;transform:translateX(-50%);text-align:center}
.brand-mark{width:72px;height:72px;border-radius:50%;background:var(--gold);margin:0 auto 6px}
.brand-name{font-family:var(--head);font-size:24px;color:var(--gold-dark);letter-spacing:1px;font-weight:400}
.search{position:absolute;right:0;top:18px;width:267px}
.search label{font-size:14px;display:block;margin-bottom:6px}
.search .field{display:flex;height:44px;border:1px solid #cfcfcf}
.search .field span{flex:1;font-size:13px;color:#888;padding:13px 10px}
.search .field i{width:44px;background:var(--gold);display:flex;align-items:center;justify-content:center}

/* nav */
.nav{height:62px;border-bottom:1px solid var(--rule)}
.nav ul{list-style:none;display:flex;justify-content:space-between;height:62px;align-items:center;padding:0 20px;font-family:var(--head);font-size:15px}
.nav li.active{color:var(--gold)}

/* hero */
.hero{height:470px;background:
  radial-gradient(ellipse 260px 300px at 290px 230px,#e8c8ad 0%,#d8b296 35%,rgba(230,226,218,0) 75%),
  radial-gradient(ellipse 120px 150px at 260px 150px,#3a2a22 0%,rgba(58,42,34,.6) 40%,rgba(58,42,34,0) 75%),
  radial-gradient(ellipse 330px 160px at 830px 340px,#1c1a17 0%,#3b3326 35%,rgba(160,140,90,.4) 60%,rgba(240,238,232,0) 80%),
  radial-gradient(ellipse 230px 260px at 1140px 380px,#6f9a3c 0%,#9bbd68 40%,rgba(200,214,170,0) 80%),
  radial-gradient(ellipse 200px 220px at 60px 420px,#8eb35c 0%,rgba(190,210,160,0) 75%),
  linear-gradient(90deg,#e6e3dc 0%,#f4f3ef 45%,#ecebe4 75%,#dfe5d2 100%)}

/* welcome */
.welcome{height:208px;background:var(--gold);color:var(--white);text-align:center;padding-top:28px}
.welcome h1{font-family:var(--head);font-weight:300;font-size:40px}
.welcome p{font-size:13.5px;line-height:25px;margin:22px auto 0;width:1046px}
.welcome svg{margin-top:4px}

/* section titles */
.sec-title{font-family:var(--head);font-weight:300;font-size:40px;color:var(--gold);text-align:center}
.btn{display:inline-block;background:var(--gold-dark);color:var(--white);font-family:var(--head);font-size:17px;text-align:center}

/* featured */
.featured{height:609px;padding-top:42px}
.products{display:flex;margin-top:38px;border-bottom:1px solid var(--rule);padding-bottom:12px}
.product{flex:1;text-align:center;border-left:1px solid var(--rule)}
.product:first-child{border-left:none}
.product .shot{width:180px;height:206px;margin:0 auto}
.shot.scrub{background:radial-gradient(ellipse 30px 90px at 70px 110px,#fbfaf6 0%,#e9e4d6 60%,rgba(255,255,255,0) 100%),radial-gradient(ellipse 36px 90px at 118px 100px,#2b2620 0%,#5c4e33 55%,rgba(255,255,255,0) 100%),#ffffff}
.shot.body{background:radial-gradient(ellipse 70px 40px at 90px 70px,#1f1d1a 0%,#3a3428 55%,rgba(255,255,255,0) 100%),radial-gradient(ellipse 85px 55px at 90px 150px,#b9a06a 0%,#8d7a4b 55%,rgba(255,255,255,0) 100%),#ffffff}
.shot.eye{background:radial-gradient(ellipse 26px 40px at 90px 55px,#1d1c1c 0%,#3d3a36 60%,rgba(255,255,255,0) 100%),radial-gradient(ellipse 30px 70px at 90px 130px,#f7f7f5 0%,#d9d8d3 60%,rgba(255,255,255,0) 100%),#ffffff}
.shot.lip{background:radial-gradient(ellipse 55px 26px at 90px 60px,#1f1d1a 0%,#46402f 60%,rgba(255,255,255,0) 100%),radial-gradient(ellipse 60px 40px at 90px 115px,#e9a6b8 0%,#b7c07a 50%,rgba(255,255,255,0) 100%),radial-gradient(ellipse 60px 30px at 90px 165px,#2a2724 0%,#5b5244 55%,rgba(255,255,255,0) 100%),#ffffff}
.product h3{font-family:var(--head);font-weight:400;font-size:21px;margin-top:18px}
.product h3.alt{color:var(--gold)}
.product .price{font-size:12px;color:var(--muted);margin-top:6px}
.product .btn{width:153px;height:52px;line-height:52px;margin-top:16px}
.center-btn{text-align:center;margin-top:13px}
.center-btn .btn{width:156px;height:54px;line-height:54px}

/* about */
.about{height:457px;background:var(--gold);color:var(--white);position:relative}
.about .text{position:absolute;left:77px;top:40px;width:660px}
.about h2{font-family:var(--head);font-weight:300;font-size:40px}
.about p{font-size:13px;line-height:25px;margin-top:8px}
.about h2+p{margin-top:18px}
.outline-btn{display:inline-block;border:1px solid var(--white);width:168px;height:55px;line-height:53px;text-align:center;font-family:var(--head);font-size:17px;margin-top:20px}
.about .leaf{position:absolute;left:742px;top:42px;width:384px;height:396px;background:
  radial-gradient(ellipse 150px 60px at 200px 110px,#d8eab0 0%,#9cc65a 50%,rgba(155,134,80,0) 100%),
  radial-gradient(ellipse 170px 90px at 210px 230px,#a8d06a 0%,#6e9f35 55%,rgba(155,134,80,0) 100%),
  radial-gradient(ellipse 160px 40px at 170px 330px,#8a5a30 0%,#6a4325 55%,rgba(155,134,80,0) 100%)}

/* treatments */
.treatments{height:582px;padding-top:44px}
.cards{display:flex;gap:10px;margin-top:40px}
.card{flex:1;background:var(--light);border-bottom:3px solid var(--gold);height:320px;text-align:center}
.card .photo{height:174px}
.photo.sun{background:radial-gradient(ellipse 110px 60px at 110px 120px,#e4b99a 0%,#c99a7a 50%,rgba(255,255,255,0) 100%),radial-gradient(ellipse 60px 40px at 200px 60px,#a9c47a 0%,rgba(255,255,255,0) 100%),linear-gradient(180deg,#f5f3ee,#e9e6de)}
.photo.acne{background:radial-gradient(ellipse 70px 90px at 70px 90px,#d9a48e 0%,#c48a74 55%,rgba(240,236,230,0) 100%),radial-gradient(ellipse 70px 90px at 190px 90px,#f0d3c0 0%,#e2bba4 55%,rgba(240,236,230,0) 100%),#f1ede8}
.photo.sensitive{background:radial-gradient(ellipse 70px 90px at 170px 90px,#f1d4c0 0%,#dcb59d 55%,rgba(250,250,250,0) 100%),radial-gradient(ellipse 40px 50px at 60px 60px,#d7dadb 0%,rgba(250,250,250,0) 100%),#fafafa}
.photo.ibs{background:radial-gradient(ellipse 120px 110px at 128px 100px,#f0cbb6 0%,#deac93 55%,rgba(250,246,242,0) 100%),radial-gradient(ellipse 40px 20px at 128px 20px,#c33b46 0%,rgba(250,246,242,0) 100%),#f8f3ef}
.card h3{font-family:var(--head);font-weight:400;font-size:19px;margin-top:24px}
.card p{font-size:12.5px;line-height:20px;color:var(--ink);padding:10px 16px 0}
.treatments .center-btn{margin-top:19px}

/* success */
.success{height:259px;background:var(--gold);color:var(--white)}
.success .wrap{height:259px}
.success h2{position:absolute;left:0;top:70px;width:214px;text-align:center;font-family:var(--head);font-weight:300;font-size:40px;line-height:48px}
.success .divider{position:absolute;left:277px;top:26px;width:1px;height:204px;background:var(--gold-line)}
.avatar{position:absolute;left:314px;top:57px;width:134px;height:134px;border-radius:50%;border:4px solid var(--white);background:radial-gradient(ellipse 45px 55px at 62px 72px,#efcdb5 0%,#d9a98a 60%,#4a3226 100%)}
.quote{position:absolute;left:472px;top:62px;width:622px;font-size:13.5px;line-height:25px}
.quote cite{display:block;font-style:normal;margin-top:12px}
.dots{position:absolute;left:475px;top:210px;display:flex;gap:7px}
.dots i{width:15px;height:15px;border-radius:50%;border:1px solid var(--white)}
.dots i.on{background:var(--white)}

/* media */
.media{height:475px;padding-top:44px}
.covers{display:flex;justify-content:space-between;margin-top:40px;padding:0 40px}
.cover{width:183px;text-align:center}
.cover .art{height:240px}
.art.one{background:radial-gradient(ellipse 60px 40px at 92px 40px,#d2304f 0%,rgba(240,200,210,0) 100%),radial-gradient(ellipse 70px 70px at 100px 160px,#fbf4ef 0%,#e8b7c4 55%,rgba(220,120,150,0) 100%),linear-gradient(180deg,#f0c9d3,#d86a8a)}
.art.two{background:radial-gradient(ellipse 60px 80px at 92px 120px,#7a4a32 0%,#a8352c 55%,rgba(200,60,50,0) 100%),linear-gradient(180deg,#e0493c,#b8322a 70%,#f3f0ea)}
.art.three{background:radial-gradient(ellipse 40px 50px at 60px 80px,#2c2a26 0%,rgba(255,255,255,0) 100%),radial-gradient(ellipse 40px 60px at 140px 120px,#a8c478 0%,rgba(255,255,255,0) 100%),linear-gradient(180deg,#ffffff,#f1f0ea)}
.art.four{background:radial-gradient(ellipse 70px 60px at 95px 100px,#e8c2a8 0%,rgba(120,80,160,0) 100%),linear-gradient(180deg,#cf3f78,#6b4da0 60%,#3a64b0)}
.cover h3{font-family:var(--head);font-weight:400;font-size:19px;margin-top:20px}
.cover .date{font-size:12px;color:var(--muted);margin-top:6px}

/* footer */
.footer{height:359px;background:var(--gold);color:var(--white)}
.footer .wrap{height:359px}
.footer h2{font-family:var(--head);font-weight:300;font-size:34px;position:absolute;top:44px}
.links{position:absolute;left:59px;top:98px;display:grid;grid-template-columns:228px 228px;column-gap:64px;list-style:none;font-size:13px}
.links li{height:37px;line-height:30px;border-bottom:1px solid var(--gold-line)}
.links li.gap{border-bottom:none}
.footer .vline{position:absolute;left:645px;top:36px;width:1px;height:285px;background:var(--gold-line)}
.contact{position:absolute;left:702px;top:98px;font-size:13px;line-height:21px;width:330px}
.contact li{list-style:none;display:flex;gap:14px;margin-bottom:14px}
.contact li svg{flex:none;margin-top:3px}
.social{width:44px;height:44px;border-radius:50%;background:var(--white)}
.copyright{height:62px;background:var(--gold-dark);color:var(--white);font-size:13px;text-align:center;line-height:62px}
</style>
</head>
<body>

<div class="topbar">
  <div class="wrap">
    <div class="follow">Follow Us On : <span class="dot-icon"></span></div>
    <div class="shop-links">
      <span><svg width="16" height="16" viewBox="0 0 16 16"><path d="M3 5h10l-1 10H4z" fill="none" stroke="#fff" stroke-width="1.5"/><path d="M5.5 5V3.5a2.5 2.5 0 0 1 5 0V5" fill="none" stroke="#fff" stroke-width="1.5"/></svg>Shopping bag</span>
      <span><svg width="18" height="16" viewBox="0 0 18 16"><path d="M1 2h3l2 8h9l2-6H5" fill="none" stroke="#fff" stroke-width="1.5"/><circle cx="7" cy="13.5" r="1.5" fill="#fff"/><circle cx="14" cy="13.5" r="1.5" fill="#fff"/></svg>My Cart</span>
      <span><svg width="16" height="16" viewBox="0 0 16 16"><path d="M2 8h10M8 4l4 4-4 4" fill="none" stroke="#fff" stroke-width="1.6"/></svg>Checkout</span>
    </div>
  </div>
</div>

<header class="header">
  <div class="wrap">
    <div class="call">
      <svg width="42" height="42" viewBox="0 0 24 24"><path d="M6.6 10.8a15.1 15.1 0 0 0 6.6 6.6l2.2-2.2a1 1 0 0 1 1-.25 11.4 11.4 0 0 0 3.6.57 1 1 0 0 1 1 1V20a1 1 0 0 1-1 1A17 17 0 0 1 3 4a1 1 0 0 1 1-1h3.5a1 1 0 0 1 1 1c0 1.25.2 2.45.57 3.57a1 1 0 0 1-.25 1z" fill="#85723f"/></svg>
      <div><small>Call Us Now</small><strong>(02) 5550 1234</strong></div>
    </div>
    <div class="brand">
      <div class="brand-mark"></div>
      <div class="brand-name">LARKSPUR</div>
    </div>
    <div class="search">
      <label>Search</label>
      <div class="field"><span>- All Categories -</span><i><svg width="14" height="10" viewBox="0 0 14 10"><path d="M0 0h14L7 10z" fill="#fff"/></svg></i></div>
    </div>
  </div>
</header>

<nav class="nav">
  <ul class="wrap">
    <li class="active">HOME</li><li>ABOUT US</li><li>PRODUCTS</li><li>ABOUT ALOE</li><li>TREATMENTS</li><li>MEDIA</li><li>SUCCESS STORIES</li><li>STOCKISTS</li><li>CONTACT US</li>
  </ul>
</nav>

<section class="hero" role="img" aria-label="Banner photograph of the brand model beside jars and tubes of skincare products among aloe leaves"></section>

<section class="welcome">
  <h1>Welcome To Larkspur Cosmetics</h1>
  <p>Larkspur Cosmetics produces a range of premium natural skincare products based on the healing and soothing Aloe Vera plant to assist people with eczema, psoriasis, dermatitis, acne, pigmentation and those looking for effective natural skincare and daily tonic.</p>
  <svg width="18" height="16" viewBox="0 0 18 16"><path d="M2 2l7 6 7-6M2 8l7 6 7-6" fill="none" stroke="#fff" stroke-width="2"/></svg>
</section>

<section class="featured">
  <div class="wrap">
    <h2 class="sec-title">Featured Products</h2>
    <div class="products">
      <div class="product"><div class="shot scrub" role="img" aria-label="Facial scrub tube standing beside its dark box"></div><h3 class="alt">Exfoliating Facial Scrub</h3><div class="price">Price : $24.95</div><a class="btn">ADD TO CART</a></div>
      <div class="product"><div class="shot body" role="img" aria-label="Body balm jar resting on its gold box"></div><h3>Aloe Vera - Body Balm</h3><div class="price">Price : $24.95</div><a class="btn">ADD TO CART</a></div>
      <div class="product"><div class="shot eye" role="img" aria-label="Eye balm bottle with black cap"></div><h3>Eye Balm</h3><div class="price">Price : $24.95</div><a class="btn">ADD TO CART</a></div>
      <div class="product"><div class="shot lip" role="img" aria-label="Stack of coloured lip balm tins"></div><h3>Aloe Vera - Lip Balm</h3><div class="price">Price : $24.95</div><a class="btn">ADD TO CART</a></div>
    </div>
    <div class="center-btn"><a class="btn">VIEW ALL</a></div>
  </div>
</section>

<section class="about">
  <div class="text">
    <h2>About Aloe</h2>
    <p>There are over 300 different species of this plant. However, it is the species Aloe Barbadensis Miller that is the most effective for consumption.</p>
    <p>Aloe vera is a rich source of vitamins, minerals, enzymes and amino acids and has been renowned for thousands of years across many cultures for its overall health benefits.<br>Vitamins: Vitamin A, B1, B2, B3, B6, B12, Folic Acid, Niacin</p>
    <p>These essential substances are a valuable addition to the other active ingredients of Aloe Vera contributing to well-being and health. Your body needs vitamins to function properly which makes them really important substances.</p>
    <a class="outline-btn">KNOW MORE</a>
  </div>
  <div class="leaf" role="img" aria-label="Sliced aloe vera leaves on a wooden dish"></div>
</section>

<section class="treatments">
  <div class="wrap">
    <h2 class="sec-title">Our Best Treatments</h2>
    <div class="cards">
      <div class="card"><div class="photo sun" role="img" aria-label="Woman receiving a soothing aloe treatment"></div><h3>After Sun Care</h3><p>Sunburn occurs when exposure to UV light exceeds the protective capacity of an individual.</p></div>
      <div class="card"><div class="photo acne" role="img" aria-label="Before and after view of skin with acne"></div><h3>Acne</h3><p>Acne is a skin condition caused by changes in the skin structures consisting of a hair.</p></div>
      <div class="card"><div class="photo sensitive" role="img" aria-label="Woman checking her sensitive skin in a mirror"></div><h3>Sensitive Skin</h3><p>Those with sensitive skin must be very careful to use the appropriate skincare for their .</p></div>
      <div class="card"><div class="photo ibs" role="img" aria-label="Hands forming a heart over a stomach"></div><h3>Irritable Bowel Syndrome</h3><p>IBS is a functional bowel disorder of the gastrointestinal (GI) tract characterized by recurrent.</p></div>
    </div>
    <div class="center-btn"><a class="btn">VIEW ALL</a></div>
  </div>
</section>

<section class="success">
  <div class="wrap">
    <h2>Success<br>Stories</h2>
    <div class="divider"></div>
    <div class="avatar" role="img" aria-label="Portrait of a customer"></div>
    <blockquote class="quote">"I have thick curly hair and had persistent problems with a dry flaky scalp. Using the Larkspur Cosmetics Gel as a shampoo has stopped the itching and flaking and the embarrassing dandruff that resulted."<cite>- Jenna Hale, Westbury NSW</cite></blockquote>
    <div class="dots"><i></i><i class="on"></i><i></i><i></i><i></i><i></i></div>
  </div>
</section>

<section class="media">
  <div class="wrap">
    <h2 class="sec-title">Media</h2>
    <div class="covers">
      <div class="cover"><div class="art one" role="img" aria-label="Magazine cover with a pink dessert"></div><h3>Weekly Notes Magazine</h3><div class="date">August 22, 2011</div></div>
      <div class="cover"><div class="art two" role="img" aria-label="Red beauty magazine cover"></div><h3>Salon Beauty Magazine</h3><div class="date">January, 2011</div></div>
      <div class="cover"><div class="art three" role="img" aria-label="Magazine page featuring the skincare range"></div><h3>Weekly Notes Magazine</h3><div class="date">August 22, 2011</div></div>
      <div class="cover"><div class="art four" role="img" aria-label="Colourful home and garden magazine cover"></div><h3>Home &amp; Garden Living</h3><div class="date">January, 2011</div></div>
    </div>
  </div>
</section>

<footer class="footer">
  <div class="wrap">
    <h2 style="left:59px">Usfull links</h2>
    <ul class="links">
      <li>Home</li><li>Media</li>
      <li>About us</li><li>Success Stories</li>
      <li>Products</li><li>Stockists</li>
      <li>About Aloe</li><li>Contact Us</li>
      <li>Treatments</li><li class="gap"></li>
    </ul>
    <div class="vline"></div>
    <h2 style="left:702px">Contact Information</h2>
    <ul class="contact">
      <li><svg width="12" height="16" viewBox="0 0 12 16"><path d="M6 0a6 6 0 0 1 6 6c0 4-6 10-6 10S0 10 0 6a6 6 0 0 1 6-6z" fill="#fff"/><circle cx="6" cy="6" r="2.2" fill="#9b8650"/></svg><span>Larkspur Cosmetics Pty Ltd<br>ABN 00 000 000 000 Unit 4/2 Fernleigh<br>Street, Westbury NSW 2000</span></li>
      <li><svg width="14" height="14" viewBox="0 0 24 24"><path d="M6.6 10.8a15.1 15.1 0 0 0 6.6 6.6l2.2-2.2a1 1 0 0 1 1-.25 11.4 11.4 0 0 0 3.6.57 1 1 0 0 1 1 1V20a1 1 0 0 1-1 1A17 17 0 0 1 3 4a1 1 0 0 1 1-1h3.5a1 1 0 0 1 1 1c0 1.25.2 2.45.57 3.57a1 1 0 0 1-.25 1z" fill="#fff"/></svg><span>(02) 5550 1234</span></li>
      <li><svg width="14" height="14" viewBox="0 0 14 14"><rect x="1" y="4" width="12" height="8" fill="#fff"/><rect x="3" y="1" width="8" height="4" fill="none" stroke="#fff"/></svg><span>(02) 5550 1235</span></li>
      <li><svg width="15" height="12" viewBox="0 0 15 12"><rect x="0.5" y="0.5" width="14" height="11" fill="#fff"/><path d="M1 1l6.5 5L14 1" fill="none" stroke="#9b8650"/></svg><span>sales@larkspurcosmetics.example</span></li>
    </ul>
    <div class="social" style="position:absolute;left:702px;top:284px"></div>
  </div>
</footer>
<div class="copyright">© Larkspur Cosmetics Pty Ltd- 2016. All rights reserved</div>

</body>
</html>
```